Plakate für Haushaltshilfen und Alltagsbegleiter
Zielgruppe
Wir bieten haushaltsnahe Dienstleistungen (Haushaltshilfen und Altgasbegleiter) für Personen mit einem Pflegegrad 1 - 5 an.
Zielgruppe sind Personen mit einem Pflegegrad 1 - 5. Hauptsächlich ältere Menschen die Unterstützung/Betreuung im Alltag und Haushalt benötigen.
Aufgabenstellung
Wir benötigen für unsere Büroräume eine Fensterbeschriftung. Es handelt sich hier um 5 Fenster (Glasflächen) und eine Glastür. Die Vorgabe ist, dass von außen zu erkennen ist dass sich um alle Räumlichkeiten um unsere (Firma Lindwerk) Räumlichkeiten handelt. Desweiteren soll auch unser Angebot erkennbar sein.
Unser Angebot enthält: Haushaltshilfen und Alltagsbegleiter
- kostenlose Haushaltshilfe ab Pflegegrad 1
- Abrechnung mit allen Kostenträgern
Da wir keine Schilder an die Fassade anbringen können, müßen die Glasflächen dafür genutzt werden um zum Einen uns als Firma erkennbar zu machen und zum anderen unser Angebot kurz zu präsentieren.
Uns ist wichtig dass unser Logo verwendet wir und auch unsere Farben.
Desweiteren sollten an den Fenstern auch teilweise eine Sichtschutz nach innen, angebracht werden, aber eben nur teilweise also nicht das ganzen Fenster z.Bsp. mit einer Blickdichten Folie überziehen, sondern in Augenhöhe wenn Fußgänger vorbei laufen.

```html
<!DOCTYPE html>
<html lang="de">
<head>
<meta charset="utf-8">
<title>Lindwerk – Fensterbeschriftung</title>
<link rel="stylesheet" href="https://fonts.googleapis.com/css2?family=Cinzel:wght@500;600&display=swap">
<style>
  :root {
    --canvas: #f2f1ee;
    --glass: #232323;
    --brand-red: #c8001a;
    --icon-red: #d51a30;
    --white: #ffffff;
    --frame: #ffffff;
    --frame-edge: #d9d7d2;
  }
  * { box-sizing: border-box; margin: 0; padding: 0; }
  html, body { width: 1200px; height: 827px; overflow: hidden; }
  body {
    background: var(--canvas);
    font-family: "Cinzel", "Times New Roman", serif;
  }
  .window-row {
    position: absolute;
    left: 90px;
    top: 201px;
    display: flex;
    gap: 60px;
  }
  .window-decal {
    position: relative;
    width: 300px;
    height: 425px;
    background: var(--glass);
    overflow: hidden;
    box-shadow: 0 0 0 10px var(--frame), 0 0 0 11px var(--frame-edge);
  }
  .decal-shapes {
    position: absolute;
    inset: 0;
    width: 300px;
    height: 425px;
  }
  .brand-name {
    position: absolute;
    top: 44px;
    left: 0;
    right: 0;
    text-align: center;
    color: var(--brand-red);
    font-size: 24px;
    font-weight: 600;
    letter-spacing: 1px;
    line-height: 1.2;
    white-space: nowrap;
  }
  .service-band {
    position: absolute;
    top: 120px;
    left: 0;
    width: 300px;
    height: 54px;
    background: var(--brand-red);
    color: var(--white);
    font-size: 22px;
    font-weight: 500;
    letter-spacing: 1px;
    white-space: nowrap;
    display: flex;
    align-items: center;
    justify-content: center;
  }
</style>
</head>
<body>
  <main class="window-row">
    <section class="window-decal">
      <svg class="decal-shapes" viewBox="0 0 300 425">
        <circle cx="52" cy="306" r="29" fill="var(--brand-red)"/>
        <circle cx="246" cy="378" r="156" fill="none" stroke="var(--brand-red)" stroke-width="5"/>
        <circle cx="246" cy="378" r="134" fill="var(--brand-red)"/>
        <g role="img" aria-label="Piktogramm Staubsauger">
          <rect x="172" y="300" width="100" height="100" rx="8" fill="var(--icon-red)"/>
        </g>
      </svg>
      <div class="brand-name">Lindwerk</div>
      <div class="service-band">HAUSHALTSHILFE</div>
    </section>

    <section class="window-decal">
      <svg class="decal-shapes" viewBox="0 0 300 425">
        <circle cx="96" cy="257" r="22" fill="var(--brand-red)"/>
        <circle cx="58" cy="349" r="16" fill="var(--brand-red)"/>
        <circle cx="252" cy="380" r="156" fill="none" stroke="var(--brand-red)" stroke-width="5"/>
        <circle cx="252" cy="380" r="134" fill="var(--brand-red)"/>
        <g role="img" aria-label="Piktogramm Einkaufstüte">
          <rect x="188" y="290" width="90" height="108" rx="8" fill="var(--icon-red)"/>
        </g>
      </svg>
      <div class="brand-name">Lindwerk</div>
      <div class="service-band">EINKAUFSSERVICE</div>
    </section>

    <section class="window-decal">
      <svg class="decal-shapes" viewBox="0 0 300 425">
        <circle cx="59" cy="366" r="22" fill="var(--brand-red)"/>
        <circle cx="244" cy="388" r="156" fill="none" stroke="var(--brand-red)" stroke-width="5"/>
        <circle cx="244" cy="388" r="134" fill="var(--brand-red)"/>
        <g role="img" aria-label="Piktogramm Herz mit helfender Hand">
          <rect x="172" y="312" width="96" height="90" rx="8" fill="var(--icon-red)"/>
        </g>
      </svg>
      <div class="brand-name">Lindwerk</div>
      <div class="service-band">ALLTAGSBEGLEITER</div>
    </section>
  </main>
</body>
</html>
```